Velmora Consulting Business

** Please add the content information from my old business card
1. I would like to see a two sided business card with both options with the 1st Option--Tallow Spire-new WHITE BACKGROUND LOGO
2 nd Option-Tallow Spire - new BLACK- Background Logo
3rd -Option a business card with my Photo on the card
Please add the new word to the card information:
EXECUTION
AS THE OWNER'S REP
WE AIM TO ACHIEVE YOUR
INFRASTRUCTURE VISION with
OUR SPECIALIZATION & EXECUTION in:

FUNDING Planning
BUSINESS Planning
INFRASTRUCTURE Planning
PROJECT Management
Since 2012
_____________________________________________________________________
I want to get spot uv raised printing. I was liking a a nice rich white linen paper stock with black writing & NOT A COLORED CARD other than a variety of white or black cards concept

```html
<!DOCTYPE html>
<html lang="en">
<head>
<meta charset="utf-8">
<title>Velmora Consulting – Business Card</title>
<link href="https://fonts.googleapis.com/css2?family=Lato:wght@400;700;900&display=swap" rel="stylesheet">
<style>
  :root {
    --backdrop: #5b5b5b;
    --card-dark: #474747;
    --card-light: #e4e4e4;
    --ink: #1b1b1b;
    --ink-soft: #2e2e2e;
    --paper-text: #f2f2f2;
    --muted: #bdbdbd;
    --accent: #d81e3c;
    --watermark: rgba(0,0,0,0.07);
  }
  * { margin: 0; padding: 0; box-sizing: border-box; }
  html, body { width: 1200px; height: 799px; overflow: hidden; }
  body {
    background: var(--backdrop);
    font-family: "Lato", sans-serif;
    position: relative;
  }
  .card {
    position: absolute;
    top: 245px;
    width: 540px;
    height: 309px;
    border-radius: 3px;
    box-shadow: 0 10px 28px rgba(0,0,0,0.35);
    overflow: hidden;
  }
  /* ---------- back side ---------- */
  .card-back { left: 30px; background: var(--card-dark); color: var(--paper-text); }
  .card-back .brand {
    position: absolute; left: 34px; top: 118px;
    font-weight: 900; font-size: 34px; line-height: 1.05;
    color: var(--muted); letter-spacing: 0.5px;
  }
  .card-back .pitch {
    position: absolute; left: 262px; top: 58px; width: 260px;
    font-size: 11.5px; line-height: 1.35; letter-spacing: 0.3px;
  }
  .pitch .claim { font-weight: 900; text-transform: uppercase; }
  .pitch .claim .lower { text-transform: none; }
  .card-back .rule {
    width: 34px; height: 2px; background: var(--accent); margin: 10px 0 8px;
  }
  .services { list-style: none; font-size: 11.5px; line-height: 1.4; }
  .services b { font-weight: 900; text-transform: uppercase; }
  .services span { font-weight: 400; color: var(--muted); text-transform: none; }
  .card-back .since {
    position: absolute; right: 26px; bottom: 24px;
    font-size: 10px; color: var(--muted);
  }
  /* ---------- front side ---------- */
  .card-front { left: 630px; background: var(--card-light); color: var(--ink); }
  .card-front .watermark {
    position: absolute; left: 24px; top: 218px;
    font-weight: 900; font-size: 78px; line-height: 1;
    color: var(--watermark);
  }
  .card-front .name {
    position: absolute; left: 30px; top: 62px;
    font-weight: 900; font-size: 25px; color: var(--ink);
  }
  .card-front .role {
    position: absolute; left: 30px; top: 96px;
    font-size: 12.5px; color: var(--accent);
    text-transform: uppercase; letter-spacing: 0.4px;
  }
  .card-front .divider {
    position: absolute; left: 30px; right: 30px; top: 122px;
    height: 1.5px; background: var(--ink-soft);
  }
  .contacts {
    position: absolute; left: 30px; top: 140px; list-style: none;
    font-size: 13px; line-height: 1; color: var(--ink-soft);
  }
  .contacts li { display: flex; align-items: center; gap: 9px; margin-bottom: 9px; }
  .contacts svg { width: 11px; height: 11px; flex: none; }
  .card-front .brand {
    position: absolute; right: 30px; top: 152px;
    font-weight: 900; font-size: 26px; line-height: 1.05;
    color: var(--ink); text-align: right;
  }
  .locations {
    position: absolute; right: 30px; bottom: 26px; list-style: none;
    font-size: 12.5px; line-height: 1; text-align: right; color: var(--ink-soft);
  }
  .locations li { display: flex; justify-content: flex-end; align-items: center; gap: 7px; margin-top: 7px; }
  .locations svg { width: 9px; height: 12px; }
</style>
</head>
<body>

<section class="card card-back" aria-label="Card back">
  <div class="brand">Velmora<br>Consulting</div>
  <div class="pitch">
    <div class="claim">
      <p>Execution</p>
      <p>As the owner's rep</p>
      <p>We aim to achieve your</p>
      <p>Infrastructure vision <span class="lower">with</span></p>
      <p>Our specialization &amp; execution <span class="lower">in:</span></p>
    </div>
    <div class="rule"></div>
    <ul class="services">
      <li><b>Funding</b> <span>Planning</span></li>
      <li><b>Business</b> <span>Planning</span></li>
      <li><b>Infrastructure</b> <span>Planning</span></li>
      <li><b>Project</b> <span>Management</span></li>
    </ul>
  </div>
  <p class="since">Since 2012</p>
</section>

<section class="card card-front" aria-label="Card front">
  <div class="watermark" aria-hidden="true">Velmora</div>
  <h1 class="name">Renata Holloway-Vance</h1>
  <p class="role">CEO / Lead Project Manager</p>
  <div class="divider"></div>
  <ul class="contacts">
    <li>
      <svg viewBox="0 0 12 12"><rect x="3" y="0.5" width="6" height="11" rx="1.2" fill="var(--accent)"/><rect x="4.2" y="2" width="3.6" height="6.5" fill="var(--card-light)"/></svg>
      867.555.0142
    </li>
    <li>
      <svg viewBox="0 0 12 12"><rect x="0.5" y="2" width="11" height="8" fill="var(--accent)"/><path d="M0.8 2.4 L6 6.6 L11.2 2.4" stroke="var(--card-light)" stroke-width="1" fill="none"/></svg>
      renata@velmora.ca
    </li>
    <li>
      <svg viewBox="0 0 12 12"><circle cx="6" cy="6" r="5.5" fill="var(--accent)"/><ellipse cx="6" cy="6" rx="2.3" ry="5.3" stroke="var(--card-light)" stroke-width="0.9" fill="none"/><line x1="0.6" y1="6" x2="11.4" y2="6" stroke="var(--card-light)" stroke-width="0.9"/></svg>
      velmora.ca
    </li>
  </ul>
  <div class="brand">Velmora<br>Consulting</div>
  <ul class="locations">
    <li>Harrow Bay NT
      <svg viewBox="0 0 9 12"><path d="M4.5 0.5 A4 4 0 0 1 8.5 4.5 C8.5 7.3 4.5 11.5 4.5 11.5 C4.5 11.5 0.5 7.3 0.5 4.5 A4 4 0 0 1 4.5 0.5 Z" fill="var(--accent)"/><circle cx="4.5" cy="4.5" r="1.5" fill="var(--card-light)"/></svg>
    </li>
    <li>Corbin Falls NB
      <svg viewBox="0 0 9 12"><path d="M4.5 0.5 A4 4 0 0 1 8.5 4.5 C8.5 7.3 4.5 11.5 4.5 11.5 C4.5 11.5 0.5 7.3 0.5 4.5 A4 4 0 0 1 4.5 0.5 Z" fill="var(--accent)"/><circle cx="4.5" cy="4.5" r="1.5" fill="var(--card-light)"/></svg>
    </li>
  </ul>
</section>

</body>
</html>
```